Business Card Design for BrightvaleMedia.com

--I need a business card design for my company BrightvaleMedia.com

I have attached my logo...I want the brightvale media logo on the front of the business card, and then I want The Quillstone Chief on the back of it with my information.

I would like to see a light colored background as well as a dark colored background

FRONT:
BRIGHTVALE MEDIA LOGO
248 N. Larkmoor
3rd Floor
San Diego CA 92173
www.BrightvaleMedia.com

Advanced Website & App Development
Websites, Apps, Online Voucher Systems

Leading Edge Marketing Services
SMS, VB, SMM, SEM,

BACK:
QUILLSTONE CHIEF LOGO
Dorian Pelletta
The Quillstone Chief
Call Or Text: 619-555-0148
Dorian@QuillstoneChief.example
www.QuillstoneChief.example

Target Market(s)

small business owners

Industry/Entity Type

Business Consultant

Contact Information for Business Card

FRONT:
BRIGHTVALE MEDIA LOGO
248 N. Larkmoor
3rd Floor
San Diego CA 92173
www.BrightvaleMedia.com

SMS, VB, SMM, SEM,

BACK:
QUILLSTONE CHIEF LOGO
Dorian Pelletta
The Quillstone Chief
Dorian@QuillstoneChief.example
www.QuillstoneChief.example

Requirements
Must have
• add this quote on it somewhere, anywhere,preferrably on back
• "The Fastest Way To Success Is To Take Action”
• — Dorian Pelletta, Quillstone Chief
Nice to have
• open
Should not have
• red

```html
<!DOCTYPE html>
<html lang="en">
<head>
<meta charset="utf-8">
<title>Brightvale Media – Business Cards</title>
<link rel="stylesheet" href="https://fonts.googleapis.com/css2?family=Source+Sans+3:ital,wght@0,400;0,600;0,700;1,400&display=swap">
<style>
  :root {
    --backdrop: #2b2b2b;
    --card-white: #ffffff;
    --brand-blue: #0a6ea8;
    --ink-dark: #333333;
    --ink-black: #050505;
    --text-white: #ffffff;
    --text-soft: #cfd8de;
    --card-shadow: rgba(0, 0, 0, 0.45);
  }
  * { margin: 0; padding: 0; box-sizing: border-box; }
  html, body {
    width: 1200px;
    height: 900px;
    overflow: hidden;
  }
  body {
    position: relative;
    background: var(--backdrop);
    font-family: "Source Sans 3", "Segoe UI", Arial, sans-serif;
  }
  .card {
    position: absolute;
    width: 347px;
    height: 561px;
    background: var(--card-white);
    overflow: hidden;
    box-shadow: 0 4px 14px var(--card-shadow);
    text-align: center;
  }
  .card--chief { left: 237px; top: 170px; }
  .card--agency { left: 649px; top: 182px; }

  .wordmark {
    position: absolute;
    left: 0;
    width: 100%;
    font-weight: 600;
    color: var(--brand-blue);
    letter-spacing: 0.06em;
    line-height: 1;
    font-size: 30px;
  }
  .card--chief .wordmark { top: 64px; }
  .card--agency .wordmark { top: 62px; }

  .holder-name {
    position: absolute;
    top: 172px; left: 0; width: 100%;
    font-size: 22px; font-weight: 700;
    color: var(--brand-blue);
  }
  .holder-title {
    position: absolute;
    top: 199px; left: 0; width: 100%;
    font-size: 20px; font-weight: 400;
    color: var(--brand-blue);
  }
  .contact-band {
    position: absolute;
    top: 271px; left: 0;
    width: 100%; height: 140px;
    background: var(--brand-blue);
  }
  .contact-list {
    position: absolute;
    top: 47px; left: 0; width: 100%;
    font-size: 15px; line-height: 23px;
    color: var(--text-white);
  }
  .contact-list .label { font-weight: 700; font-size: 16px; margin-right: 6px; }
  .footer-band {
    position: absolute;
    top: 411px; left: 0;
    width: 100%; height: 150px;
    background: var(--ink-black);
  }
  .footer-band .site {
    position: absolute;
    top: 65px; left: 0; width: 100%;
    font-size: 15px;
    color: var(--text-white);
  }
  .motto {
    position: absolute;
    top: 100px; left: 20px; right: 20px;
    font-size: 12px; line-height: 16px;
    font-style: italic;
    color: var(--text-soft);
  }
  .motto cite { display: block; font-style: normal; }

  .agency-blue {
    position: absolute;
    top: 212px; left: 0;
    width: 100%; height: 349px;
    background: var(--brand-blue);
    border-radius: 22px 22px 0 0;
  }
  .agency-panel {
    position: absolute;
    left: 21px; width: 305px;
    background: var(--card-white);
  }
  .agency-panel--info { top: 150px; height: 246px; }
  .agency-panel--site { top: 477px; height: 84px; }
  .agency-info {
    position: absolute;
    top: 197px; left: 0; width: 100%;
    font-size: 15px; line-height: 21px;
    color: var(--ink-dark);
  }
  .agency-info p + p { margin-top: 23px; }
  .agency-site {
    position: absolute;
    top: 500px; left: 0; width: 100%;
    font-size: 15px;
    color: var(--ink-dark);
  }
</style>
</head>
<body>

  <section class="card card--chief" aria-label="Quillstone Chief personal card">
    <div class="wordmark">QUILLSTONE CHIEF</div>
    <h1 class="holder-name">Dorian Pelletta</h1>
    <p class="holder-title">The Quillstone Chief</p>
    <div class="contact-band">
      <div class="contact-list">
        <p><span class="label">P:</span>619-555-0148</p>
        <p><span class="label">W:</span>Dorian@QuillstoneChief.example</p>
      </div>
    </div>
    <div class="footer-band">
      <p class="site">www.QuillstoneChief.example</p>
      <blockquote class="motto">
        “The Fastest Way To Success Is To Take Action”
        <cite>— Dorian Pelletta, Quillstone Chief</cite>
      </blockquote>
    </div>
  </section>

  <section class="card card--agency" aria-label="Brightvale Media company card">
    <div class="agency-blue"></div>
    <div class="agency-panel agency-panel--info"></div>
    <div class="agency-panel agency-panel--site"></div>
    <div class="wordmark">BRIGHTVALE MEDIA</div>
    <div class="agency-info">
      <p>248 N. Larkmoor<br>3rd Floor, San Diego CA 92173</p>
      <p>Advanced Website &amp; App Development<br>Websites, Apps, Online Voucher Systems</p>
      <p>Leading Edge Marketing Services<br>SMS | VB | SMM | SEM</p>
    </div>
    <p class="agency-site">www.BrightvaleMedia.com</p>
  </section>

</body>
</html>
```